Veltrane Group Business Card Design

The CEO is looking for a new trendy look for his business card.
You can stay with current branding or come up with something new/creative. It can be 3D, including Medical Office buildings. You can use our logo in a variety of colors. Please include name, title, company name, company website, email address, cell number

Target Market(s)

Real Estate Development and Construction

Industry/Entity Type

Health care real estate

Contact Information for Business Card

Rohesh Kamdar, CEO M-604.781.2249 E-roheshkamdar@veltrane.com Address:4180 Lindqvist Ave, Tampa, FL 33482 www.veltrane.com

Font styles to use
Other font styles liked:
• Be creative

Requirements
Must have
• Creative, trendy look
Nice to have
• Please go to our website to get a feel- www. veltrane.com
Should not have
• small fonts

```html
<!DOCTYPE html>
<html lang="en">
<head>
<meta charset="utf-8">
<title>Veltrane Group Business Card</title>
<link href="https://fonts.googleapis.com/css2?family=Archivo:wght@400;600;700;900&display=swap" rel="stylesheet">
<style>
  :root {
    --stage: #3a3a3c;
    --brand-red: #b01f2b;
    --brand-red-light: #c8404c;
    --navy: #1d2a4d;
    --paper: #ffffff;
    --ink-light: #ffffff;
  }
  * { margin: 0; padding: 0; box-sizing: border-box; }
  html, body {
    width: 1200px;
    height: 689px;
    overflow: hidden;
    background: var(--stage);
    font-family: "Archivo", Arial, sans-serif;
  }
  .stage {
    position: relative;
    width: 1200px;
    height: 689px;
  }
  .card {
    position: absolute;
    top: 194px;
    width: 525px;
    height: 300px;
    border-radius: 18px;
    overflow: hidden;
    box-shadow: 0 14px 30px rgba(0,0,0,0.35);
  }
  /* Back of card */
  .card--back {
    left: 45px;
    background: var(--brand-red);
    display: flex;
    align-items: center;
    justify-content: center;
  }
  .wordmark {
    font-weight: 900;
    letter-spacing: -1px;
    line-height: 1;
    white-space: nowrap;
  }
  .card--back .wordmark {
    font-size: 54px;
    color: var(--brand-red-light);
  }
  /* Front of card */
  .card--front {
    left: 630px;
    background: var(--paper);
  }
  .front__logo-area {
    position: absolute;
    left: 0; top: 0;
    width: 100%;
    height: 170px;
    display: flex;
    align-items: center;
    justify-content: center;
  }
  .card--front .wordmark {
    font-size: 50px;
    color: var(--brand-red);
  }
  .front__rule {
    position: absolute;
    left: 0; top: 170px;
    width: 100%;
    height: 4px;
    background: var(--navy);
  }
  .front__band {
    position: absolute;
    left: 0; top: 178px;
    width: 100%;
    height: 122px;
    background: var(--brand-red);
    color: var(--ink-light);
    display: flex;
    align-items: center;
    padding: 0 26px;
  }
  .identity {
    flex: 1;
    text-align: right;
    padding-right: 18px;
  }
  .identity__name {
    font-size: 22px;
    font-weight: 700;
  }
  .identity__title {
    font-size: 13px;
    font-weight: 400;
    margin-top: 2px;
  }
  .identity__address {
    font-size: 12px;
    margin-top: 10px;
  }
  .divider {
    width: 1px;
    height: 70px;
    background: rgba(255,255,255,0.7);
  }
  .contact-list {
    list-style: none;
    padding-left: 16px;
    font-size: 12.5px;
  }
  .contact-list li {
    display: flex;
    align-items: center;
    gap: 8px;
    line-height: 1.6;
  }
  .contact-list svg {
    width: 12px;
    height: 12px;
    fill: var(--ink-light);
    flex: none;
  }
</style>
</head>
<body>
<main class="stage">
  <section class="card card--back" aria-label="Card back">
    <span class="wordmark">Veltrane Group</span>
  </section>

  <section class="card card--front" aria-label="Card front">
    <div class="front__logo-area">
      <span class="wordmark">Veltrane Group</span>
    </div>
    <div class="front__rule"></div>
    <div class="front__band">
      <div class="identity">
        <p class="identity__name">Rohesh Kamdar</p>
        <p class="identity__title">CEO</p>
        <p class="identity__address">4180 Lindqvist Ave, Tampa, FL 33482</p>
      </div>
      <div class="divider"></div>
      <ul class="contact-list">
        <li>
          <svg viewBox="0 0 24 24" aria-hidden="true"><path d="M6.6 10.8a15.2 15.2 0 0 0 6.6 6.6l2.2-2.2c.3-.3.7-.4 1-.2 1.1.4 2.3.6 3.6.6.6 0 1 .4 1 1V20c0 .6-.4 1-1 1A17 17 0 0 1 3 4c0-.6.4-1 1-1h3.5c.6 0 1 .4 1 1 0 1.3.2 2.5.6 3.6.1.3 0 .7-.2 1z"/></svg>
          604.781.2249
        </li>
        <li>
          <svg viewBox="0 0 24 24" aria-hidden="true"><path d="M2 5h20v14H2zm2 2v.5l8 5 8-5V7zm0 3v7h16v-7l-8 5z"/></svg>
          roheshkamdar@veltrane.com
        </li>
        <li>
          <svg viewBox="0 0 24 24" aria-hidden="true"><circle cx="12" cy="12" r="10"/></svg>
          www.veltrane.com
        </li>
      </ul>
    </div>
  </section>
</main>
</body>
</html>
```